laser type of light point of purchase package box

This is a box design for a special effect laser light product. There is a (lid) top, two sides, and a front and back. The measurements of the sides are 4 5/8 x 3 3/8. The front and back are 5 1/4 x 3 3/8. The top lid is 5 1/4 x 4 3/4. I have included a somewhat template that the company gave me from another persons packaging. We are trying to express the multiple uses of the product. While using the unit outside it cannot get wet or rained on must be under cover or brought back indoors. The product projects laser beams in different patterns available.
I have increased my budget how about some entries???
Target Market(s)
Target market is mainly over age 40
Industry/Entity Type
It Company
Requirements
Must have
- Must have on box somewhere on side "made in china"
Must have on box the safety warning symbols that are on the sample template enclosed. (not sure of all meanings but make sure have one that denotes to keep away from young children)
Must have "Special effect holographic laser pattern light"
Must have logo on it that I have enclosed.
Must have website BRAMBLEGLOWS.EXAMPLE
Must have email address BRAMBLEGLOWS@MAILBOX.EXAMPLE
Must have the line: "Unlimited possibilities to beautify your life!
Limited only by your imagination"
I want to make a list of possible uses somewhere on the box which are:
party rooms
lawns
pool enclosures
garage doors
driveways
christmas trees
rv & mobile homes
bedrooms
business ambiance
bars & nightclubs
car & boat display
motorcycle display
YOU NAME IT!
Nice to have
- Would like the colors in the logo used throughout ??
also list the features:
adjustable motion speed
sound activation mode
Should not have
- The disco dancers that are on sample , do not want to limit uses just to a nightclub

```html
<!DOCTYPE html>
<html lang="en">
<head>
<meta charset="utf-8">
<title>Laser Light Box – Side Panel</title>
<link href="https://fonts.googleapis.com/css2?family=Carlito:ital,wght@1,400;1,700&family=Open+Sans:wght@400;500&family=Lilita+One&display=swap" rel="stylesheet">
<style>
  :root {
    --panel-black: #050507;
    --glow-violet: #2a2140;
    --glow-green: #123a22;
    --list-green: #9ccb3b;
    --contact-green: #8dc63f;
    --burst-purple: #a35aa6;
    --ink-white: #ffffff;
    --made-top: #f7d44a;
    --made-bottom: #e2562a;
    --made-edge: #6b2a12;
  }
  * { margin: 0; padding: 0; box-sizing: border-box; }
  html, body { width: 1200px; height: 919px; overflow: hidden; background: var(--panel-black); }
  .panel {
    position: relative;
    width: 1200px; height: 919px;
    overflow: hidden;
    background: var(--panel-black);
    border-top: 2px solid #1c1c1e;
  }
  .laser-art {
    position: absolute; inset: 0;
    background:
      radial-gradient(ellipse 420px 320px at 640px 470px, var(--glow-violet) 0%, transparent 70%),
      radial-gradient(circle 160px at 660px 160px, var(--glow-green) 0%, transparent 75%),
      radial-gradient(circle 140px at 500px 650px, var(--glow-green) 0%, transparent 75%),
      radial-gradient(ellipse 700px 500px at 600px 460px, #0d1310 0%, var(--panel-black) 85%);
  }
  .uses {
    position: absolute; top: 68px;
    list-style: none;
    font-family: "Carlito", "Calibri", sans-serif;
    font-style: italic;
    font-size: 25px;
    letter-spacing: 0.3px;
    color: var(--list-green);
  }
  .uses--left { left: 88px; }
  .uses--right { left: 765px; }
  .uses li {
    display: flex; align-items: center;
    height: 46.6px;
  }
  .uses .burst { width: 24px; height: 24px; margin-right: 24px; flex: none; }
  .warning {
    position: absolute; left: 696px; top: 662px;
    font-family: "Open Sans", sans-serif;
    font-weight: 500;
    font-size: 26px;
    color: var(--ink-white);
  }
  .contact {
    position: absolute; left: 78px; top: 702px;
    font-family: "Open Sans", sans-serif;
    font-size: 24px;
    line-height: 40px;
    color: var(--contact-green);
  }
  .origin {
    position: absolute; left: 79px; top: 798px;
    font-family: "Lilita One", sans-serif;
    font-size: 33px;
    letter-spacing: 0.5px;
    background: linear-gradient(var(--made-top), var(--made-bottom));
    -webkit-background-clip: text; background-clip: text;
    color: transparent;
    -webkit-text-stroke: 1.5px var(--made-edge);
  }
  .handling {
    position: absolute; top: 737px; left: 0;
  }
  .handling__icon {
    position: absolute; top: 0;
    width: 96px; height: 108px;
    border: 3px solid var(--ink-white);
    background: var(--panel-black);
  }
  .handling__icon svg { width: 100%; height: 100%; display: block; }
  .handling__icon--fill { background: #3a3a3a; }
</style>
</head>
<body>
<main class="panel">
  <div class="laser-art" role="img" aria-label="Background of green and red laser beam streaks and starburst patterns over a dark violet glow"></div>

  <svg width="0" height="0" style="position:absolute">
    <defs>
      <symbol id="burst" viewBox="-12 -12 24 24">
        <g stroke="#a35aa6" stroke-width="2.2" stroke-linecap="round">
          <line x1="0" y1="-11" x2="0" y2="11"/>
          <line x1="-11" y1="0" x2="11" y2="0"/>
          <line x1="-8" y1="-8" x2="8" y2="8"/>
          <line x1="-8" y1="8" x2="8" y2="-8"/>
          <line x1="-4" y1="-10" x2="4" y2="10"/>
          <line x1="-10" y1="-4" x2="10" y2="4"/>
          <line x1="4" y1="-10" x2="-4" y2="10"/>
          <line x1="10" y1="-4" x2="-10" y2="4"/>
        </g>
      </symbol>
    </defs>
  </svg>

  <ul class="uses uses--left">
    <li><svg class="burst"><use href="#burst"/></svg>PARTY ROOMS</li>
    <li><svg class="burst"><use href="#burst"/></svg>LAWNS</li>
    <li><svg class="burst"><use href="#burst"/></svg>POOL ENCLOSURES</li>
    <li><svg class="burst"><use href="#burst"/></svg>GARAGE DOORS</li>
    <li><svg class="burst"><use href="#burst"/></svg>DRIVEWAYS</li>
    <li><svg class="burst"><use href="#burst"/></svg>CHRISTMAS TREES</li>
  </ul>
  <ul class="uses uses--right">
    <li><svg class="burst"><use href="#burst"/></svg>RV &amp; MOBILE HOMES</li>
    <li><svg class="burst"><use href="#burst"/></svg>BEDROOMS</li>
    <li><svg class="burst"><use href="#burst"/></svg>BUSINESS AMBIANCE</li>
    <li><svg class="burst"><use href="#burst"/></svg>BARS &amp; NIGHTCLUBS</li>
    <li><svg class="burst"><use href="#burst"/></svg>CAR &amp; BOAT DISPLAY</li>
    <li><svg class="burst"><use href="#burst"/></svg>MOTORCYCLE DISPLAY</li>
  </ul>

  <p class="warning">keep away from young children</p>

  <div class="contact">
    <p>www.BRAMBLEGLOWS.EXAMPLE</p>
    <p>BRAMBLEGLOWS@MAILBOX.EXAMPLE</p>
  </div>

  <p class="origin">MADE IN CHINA</p>

  <div class="handling">
    <div class="handling__icon" style="left:572px" aria-label="Keep dry">
      <svg viewBox="0 0 90 102" fill="none" stroke="#fff" stroke-width="3" stroke-linecap="round">
        <path d="M18 52 Q45 20 72 52 Z" fill="#fff"/>
        <path d="M45 52 V76 Q45 82 39 82 Q34 82 34 77"/>
        <g stroke-width="2"><line x1="24" y1="16" x2="22" y2="24"/><line x1="36" y1="12" x2="34" y2="20"/><line x1="48" y1="14" x2="46" y2="22"/><line x1="60" y1="12" x2="58" y2="20"/><line x1="70" y1="18" x2="68" y2="26"/><line x1="30" y1="26" x2="28" y2="32"/><line x1="56" y1="24" x2="54" y2="30"/></g>
      </svg>
    </div>
    <div class="handling__icon" style="left:683px" aria-label="This way up">
      <svg viewBox="0 0 90 102" fill="#fff">
        <path d="M30 18 L18 40 H26 V74 H34 V40 H42 Z"/>
        <path d="M60 18 L48 40 H56 V74 H64 V40 H72 Z"/>
        <rect x="16" y="80" width="58" height="5"/>
      </svg>
    </div>
    <div class="handling__icon" style="left:794px" aria-label="Fragile">
      <svg viewBox="0 0 90 102" fill="#fff">
        <path d="M28 18 H62 Q62 52 48 56 V80 H58 V85 H32 V80 H42 V56 Q28 52 28 18 Z"/>
        <path d="M46 18 L40 30 L48 36 L42 46" stroke="#050507" stroke-width="3" fill="none"/>
      </svg>
    </div>
    <div class="handling__icon" style="left:911px" aria-label="Keep away from sunlight">
      <svg viewBox="0 0 90 102" fill="none" stroke="#fff" stroke-width="2" stroke-linecap="round">
        <circle cx="45" cy="36" r="9" fill="#fff"/>
        <g><line x1="45" y1="12" x2="45" y2="22"/><line x1="45" y1="50" x2="45" y2="58"/><line x1="21" y1="36" x2="31" y2="36"/><line x1="59" y1="36" x2="69" y2="36"/><line x1="28" y1="19" x2="35" y2="26"/><line x1="55" y1="46" x2="62" y2="53"/><line x1="62" y1="19" x2="55" y2="26"/><line x1="28" y1="53" x2="35" y2="46"/></g>
        <path d="M24 72 L45 58 L66 72" stroke-width="3"/>
        <rect x="38" y="74" width="14" height="12" fill="#fff"/>
      </svg>
    </div>
    <div class="handling__icon handling__icon--fill" style="left:1025px" role="img" aria-label="Pictogram of a figure placing litter into a waste bin"></div>
  </div>
</main>
</body>
</html>
```